Residential Remodeling Contractor needs updated business card

I need a new design for my business card.
Name of the company is Ridgefell Construction. I need a card that commands presence, strength, integrity. I have been in business for 28 years. I am a Residential Remodeling Contractor that covers all aspects of a residential remodel and build.

```html
<!DOCTYPE html>
<html lang="en">
<head>
<meta charset="utf-8">
<title>Ridgefell Construction – Business Card</title>
<link href="https://fonts.googleapis.com/css2?family=Source+Serif+4:wght@600;700&family=Arimo:wght@400&display=swap" rel="stylesheet">
<style>
  :root {
    --navy: #183d7b;
    --paper: #ffffff;
    --ink: #333333;
    --backdrop: #9a9a9a;
  }
  * { margin: 0; padding: 0; box-sizing: border-box; }
  html, body { width: 1200px; height: 1059px; overflow: hidden; background: var(--backdrop); }
  .canvas { position: relative; width: 1200px; height: 1059px; }

  .card { position: absolute; border-radius: 24px; overflow: hidden; }
  .card--front { left: 256px; top: 89px; width: 688px; height: 390px; background: var(--paper); }
  .card--back { left: 253px; top: 569px; width: 694px; height: 394px; background: var(--navy); }

  .front-band { position: absolute; left: 0; right: 0; bottom: 0; height: 14px; background: var(--navy); }

  .wordmark {
    position: absolute;
    font-family: "Source Serif 4", Georgia, serif;
    font-weight: 600;
    font-variant: small-caps;
    line-height: 1;
    white-space: nowrap;
  }
  .wordmark span { display: block; }
  .mark-square { position: absolute; }

  .card--front .mark-square { left: 60px; top: 183px; width: 24px; height: 24px; background: var(--navy); }
  .card--front .wordmark { left: 104px; top: 174px; color: var(--navy); }
  .card--front .wordmark .w1 { font-size: 42px; }
  .card--front .wordmark .w2 { font-size: 33px; margin-top: 2px; }

  .card--back .mark-square { left: 148px; top: 194px; width: 40px; height: 40px; background: var(--paper); }
  .card--back .wordmark { left: 217px; top: 172px; color: var(--paper); }
  .card--back .wordmark .w1 { font-size: 66px; }
  .card--back .wordmark .w2 { font-size: 52px; margin-top: 2px; }

  .divider { position: absolute; left: 344px; top: 105px; width: 1.5px; height: 180px; background: var(--navy); }

  .contact { position: absolute; left: 370px; top: 95px; font-family: "Arimo", Arial, sans-serif; color: var(--ink); }
  .contact__name { font-family: "Source Serif 4", Georgia, serif; font-weight: 700; font-size: 26px; color: var(--navy); line-height: 1; letter-spacing: 0.2px; }
  .contact__role { font-size: 16px; margin-top: 4px; }
  .contact__address { font-size: 16px; line-height: 22px; margin-top: 18px; }
  .contact__list { list-style: none; margin-top: 14px; font-size: 16px; }
  .contact__list li { display: flex; align-items: center; height: 26.5px; }
  .contact__list svg { width: 12px; height: 12px; margin-right: 7px; fill: var(--navy); flex: none; }
</style>
</head>
<body>
<div class="canvas">

  <section class="card card--front">
    <div class="mark-square"></div>
    <div class="wordmark"><span class="w1">Ridgefell</span><span class="w2">Construction</span></div>
    <div class="divider"></div>
    <div class="contact">
      <p class="contact__name">OWEN HALVORSEN</p>
      <p class="contact__role">Owner &amp; Manager</p>
      <p class="contact__address">P.O. Box&nbsp; Street Name<br>Country Name AB, A5B 521</p>
      <ul class="contact__list">
        <li><svg viewBox="0 0 12 12" aria-hidden="true"><path d="M1 4.5C1 2.5 3 1.5 6 1.5s5 1 5 3v1H8.5V4h-5v1.5H1z M3 6h6l1.5 4.5h-9z M6 7a1.4 1.4 0 1 0 0 2.8A1.4 1.4 0 1 0 6 7z"/></svg>555 214 7390</li>
        <li><svg viewBox="0 0 12 12" aria-hidden="true"><path d="M0.5 4.5 6 1l5.5 3.5V11H0.5z M1.8 5 6 8l4.2-3L6 2.3z" /></svg>info@ridgefellconstruction.com</li>
        <li><svg viewBox="0 0 12 12" aria-hidden="true"><path d="M6 0.5a5.5 5.5 0 1 0 0 11a5.5 5.5 0 1 0 0-11z M3 3h2.5l1 1.5-1 1.5H4l-1-1.5z M7 6.5h2.5L9 9 7.5 10 7 8z" fill-rule="evenodd"/></svg>www.ridgefellconstruction.com</li>
      </ul>
    </div>
    <div class="front-band"></div>
  </section>

  <section class="card card--back">
    <div class="mark-square"></div>
    <div class="wordmark"><span class="w1">Ridgefell</span><span class="w2">Construction</span></div>
  </section>

</div>
</body>
</html>
```